Card design for orthopaedic surgeons working as The Brightwater Joint Centre

Business cards, letterhead

Colors

Designer to choose colors to be used in the design.

Requirements
Must have
• Late addition.
• Cards letterhead must have logos of
• Crestmoor Lindell College of Surgeons
• Varenwood Bone Health Association
Nice to have
• Back of card to have space for appointment time to be added by hand and some blank space for writing incidental other notes.

```html
<!DOCTYPE html>
<html lang="en">
<head>
<meta charset="utf-8">
<title>The Brightwater Joint Centre – Business Card</title>
<link href="https://fonts.googleapis.com/css2?family=Poppins:wght@300;400;600&display=swap" rel="stylesheet">
<style>
  :root {
    --backdrop: #7d7d7d;
    --sky: #33afff;
    --navy: #05304a;
    --paper: #ffffff;
    --ink-light: #ffffff;
    --badge: #d6e6f2;
  }
  html, body {
    margin: 0;
    width: 1200px;
    height: 960px;
    overflow: hidden;
    background: var(--backdrop);
    font-family: "Poppins", sans-serif;
  }
  .card {
    position: absolute;
    width: 560px;
    height: 320px;
    border-radius: 22px;
    overflow: hidden;
  }
  /* Front */
  .card-front {
    left: 110px;
    top: 110px;
    background: var(--sky);
    color: var(--ink-light);
    display: flex;
    flex-direction: column;
    align-items: center;
    justify-content: center;
  }
  .brand-name {
    font-weight: 300;
    font-size: 30px;
    letter-spacing: -0.5px;
    margin: 0;
  }
  .front-web {
    display: flex;
    align-items: center;
    gap: 12px;
    margin-top: 10px;
    font-weight: 300;
    font-size: 13px;
    letter-spacing: 3px;
  }
  .front-web .rule {
    width: 40px;
    height: 1.5px;
    background: var(--ink-light);
  }
  /* Back */
  .card-back {
    left: 530px;
    top: 520px;
    background: var(--paper);
  }
  .card-back .divider {
    position: absolute;
    inset: 0;
  }
  .back-brand {
    position: absolute;
    right: 22px;
    top: 84px;
    font-size: 17px;
    font-weight: 300;
    color: var(--sky);
    letter-spacing: -0.3px;
    margin: 0;
    white-space: nowrap;
  }
  .affiliations {
    position: absolute;
    right: 26px;
    bottom: 26px;
    display: flex;
    gap: 12px;
  }
  .affiliation-badge {
    width: 38px;
    height: 38px;
    border-radius: 50%;
    background: var(--badge);
  }
  .contact {
    position: absolute;
    left: 38px;
    top: 96px;
    color: var(--ink-light);
  }
  .person-name {
    font-weight: 600;
    font-size: 21px;
    margin: 0;
    line-height: 1.1;
  }
  .person-role {
    font-weight: 600;
    font-size: 12px;
    margin: 2px 0 12px;
  }
  .address {
    font-size: 11.5px;
    line-height: 1.45;
    margin: 0 0 10px;
  }
  .contact-list {
    list-style: none;
    padding: 0;
    margin: 0;
    font-size: 11.5px;
    line-height: 1.5;
  }
  .contact-list li {
    display: flex;
    align-items: center;
    gap: 8px;
  }
  .contact-list svg {
    width: 11px;
    height: 11px;
    fill: var(--ink-light);
    flex: none;
  }
</style>
</head>
<body>

<section class="card card-front">
  <h1 class="brand-name">The Brightwater Joint Centre</h1>
  <div class="front-web">
    <span class="rule"></span>
    <span>www.brightwaterjoint.com</span>
    <span class="rule"></span>
  </div>
</section>

<section class="card card-back">
  <svg class="divider" viewBox="0 0 560 320" preserveAspectRatio="none" aria-hidden="true">
    <path d="M178,0 H190 C205,60 270,100 310,150 C345,200 355,270 362,320 H352 C345,270 330,205 298,165 C258,115 196,75 178,0 Z" fill="var(--sky)"/>
    <path d="M0,0 H170 C185,70 250,110 290,160 C320,200 335,270 345,320 H0 Z" fill="var(--navy)"/>
  </svg>

  <p class="back-brand">The Brightwater Joint Centre</p>

  <div class="affiliations">
    <div class="affiliation-badge" role="img" aria-label="Crestmoor Lindell College of Surgeons badge"></div>
    <div class="affiliation-badge" role="img" aria-label="Varenwood Bone Health Association badge"></div>
  </div>

  <div class="contact">
    <h2 class="person-name">Daniel Harlow</h2>
    <p class="person-role">President</p>
    <p class="address">4120 Larkspur Way<br>Fairhaven, Oregon 97322</p>
    <ul class="contact-list">
      <li><svg viewBox="0 0 12 12"><path d="M2.5,1 L4.5,1 L5.2,3.5 L4,4.6 C4.6,6 6,7.4 7.4,8 L8.5,6.8 L11,7.5 L11,9.5 C11,10.3 10.3,11 9.5,11 C5,11 1,7 1,2.5 C1,1.7 1.7,1 2.5,1 Z"/></svg>541-208-7734</li>
      <li><svg viewBox="0 0 12 12"><path d="M3,0.5 H9 V11.5 H3 Z M4,1.5 V9.5 H8 V1.5 Z M5.4,10 H6.6 V11 H5.4 Z"/></svg>541-377-1926</li>
      <li><svg viewBox="0 0 12 12"><path d="M3,1 H8 V4 H3 Z M1,4.5 H11 V9 H9 V11 H3 V9 H1 Z M4,8 V10 H8 V8 Z"/></svg>541-604-2281</li>
      <li><svg viewBox="0 0 12 12"><path d="M1,2.5 H11 V9.5 H1 Z M1.6,3 L6,6.4 L10.4,3 Z"/></svg>hello@brightwaterjoint.com</li>
      <li><svg viewBox="0 0 12 12"><circle cx="6" cy="6" r="5"/></svg>www.brightwaterjoint.com</li>
    </ul>
  </div>
</section>

</body>
</html>
```